Web Site Design For Real Estate Sales Project

The idea behind this project is pretty simple. I am putting my penthouse apartment up for sale and am trying to be creative in selling it.
Technically this will be pretty simple, it will be 3 pages but graphically this has to be as impressive as possible which is why I am trying Pixel Harbor.
The apartment is located in Barra Da Tijuca, Rio De Janeiro, Brazil. (This is where the 2016 Solstice Meet will be held)
I am looking for an index page and 2 sub-pages. I am open to all kinds of designs and navigation's but it has to make an impression quickly with a professional and enticing design. The index page should make it obvious that there is a penthouse apartment for sale in Barra Da Tijuca ( suburb of Rio De Janeiro). The first sub page is about the Condominium where the apartment is located, the second sub page is about the apartment itself.
Here is a more detailed description of what the 3 pages should be about.
Index Page
This is the landing page and should make it obvious that there is an apartment for sale in Barra Da Tijuca, Rio De Janeiro with the following attributes
251 SQ M
Duplex Penthouse
4 suites
Price R$ 2.200.000
Price per SQ M: R$ 8.764
First Sub-Page
This is about the Condominium which is called "Tranquil Cliff Suites" with the following bullets
*Family friendly and safe
*Direct access to the beach
*Many amenities like pool, football court, gym, sauna
There should be some photos of the condominium and a link to the site of the condominium ( www.tcsqv.com )
Second Sub-page
This is about the apartment. It should list in bullets the features of the apartment and then have a photo gallery of the view and various rooms. I have attached sample photos but will eventually have to use more photos.
Apartment Features
Price: R$ 2.220.000
251 m2 Duplex Penthouse
4 suites
maids room with bath
guest bathroom
living room
dinning room
Terrace with heated pool for year round use
Veranda
As mentioned above I am open to all designs and navigation so feel free to be creative. The important thing is catch peoples attention and get the message across in a few seconds, which is that there is an apartment for sale at this price with these features in this location. I will then use zintra clickreach and SEO to get people to the site.
Thanks
Men and Women from 30-60 years of age.
Apartment

```html
<!DOCTYPE html>
<html lang="en">
<head>
<meta charset="utf-8">
<title>Altura Homes</title>
<link href="https://fonts.googleapis.com/css2?family=Oswald:wght@500;600&family=Arimo:wght@400&display=swap" rel="stylesheet">
<style>
  :root{
    --black:#000;
    --blue:#1a9be6;
    --blue-dark:#1d6aa5;
    --olive:#97a20c;
    --olive-line:#b5c044;
    --paper:#e9ebea;
    --ink:#3a3a3a;
    --body:#4a4a4a;
    --footer:#3a3a3a;
    --footer-text:#e6e6e6;
    --nav-grey:#8d8d8d;
    --white:#fff;
  }
  *{box-sizing:border-box;margin:0;padding:0}
  html,body{width:1067px;height:1200px;overflow:hidden}
  body{position:relative;background:var(--paper);font-family:"Arimo",Arial,sans-serif;color:var(--body)}
  .abs{position:absolute}

  .site-header{left:0;top:0;width:1067px;height:99px;background:var(--black)}
  .brand-name{left:107px;top:32px;font-family:"Oswald",sans-serif;font-weight:600;font-size:26px;letter-spacing:.3px;color:var(--blue);text-transform:uppercase}
  .main-nav{left:559px;top:35px;display:flex;align-items:center;font-family:"Oswald",sans-serif;font-weight:500;font-size:12px;text-transform:uppercase}
  .main-nav a{color:var(--nav-grey);text-decoration:none;margin-right:53px}
  .main-nav a.active{background:var(--blue);color:var(--white);border-radius:15px;width:71px;height:30px;line-height:30px;text-align:center;margin-right:38px}

  .hero{left:0;top:99px;width:1067px;height:437px;background:linear-gradient(180deg,#5e7f9a 0%,#2f6a9a 18%,#7a8c80 40%,#566b45 62%,#3e5a2a 85%,#5c6a2c 100%)}
  .hero-fact{left:107px;height:37px;line-height:37px;padding:0 10px;background:var(--black);color:var(--white);font-family:"Oswald",sans-serif;font-weight:600;font-size:26px;text-transform:uppercase;white-space:nowrap}
  .hero-fact.highlight{background:var(--blue)}
  .slider-dots{left:483px;top:510px;width:99px;height:26px;background:var(--blue);border-radius:13px 13px 0 0;display:flex;justify-content:center;align-items:center;gap:7px;padding-top:2px}
  .slider-dots i{width:12px;height:12px;border-radius:50%;background:var(--white)}
  .slider-dots i.current{background:var(--blue-dark)}

  .section-title{left:106px;font-family:"Oswald",sans-serif;font-weight:500;font-size:21px;color:var(--ink);text-transform:uppercase}
  .section-title em{font-style:normal;color:var(--blue-dark)}
  .hatch{left:106px;height:8px;background:repeating-linear-gradient(60deg,#c3c5c4 0 1px,transparent 1px 3px)}

  .photo-frame{background:var(--white);border:1px solid #d2d4d3;padding:5px}
  .photo-frame div{width:100%;height:100%}

  .intro-text{left:354px;top:620px;width:343px;font-size:10.6px;line-height:14.2px;text-align:justify}
  .intro-text p{margin-bottom:14px}

  .features{left:720px;top:549px;width:240px;height:296px;background:var(--olive);border-radius:3px;color:var(--white)}
  .features h2{font-family:"Oswald",sans-serif;font-weight:500;font-size:21px;padding:10px 0 0 37px;height:50px;border-bottom:1px dashed var(--olive-line);text-transform:uppercase}
  .features ul{list-style:none}
  .features li{position:relative;padding:15px 25px 15px 37px;font-size:12px;line-height:16px;border-bottom:1px dashed var(--olive-line)}
  .features li:last-child{border-bottom:0;padding-top:15px;text-align:justify}
  .features li::before{content:"";position:absolute;left:15px;top:18px;width:10px;height:10px;border-radius:50%;background:#7d8609}
  .features li::after{content:"";position:absolute;left:18px;top:21px;width:3px;height:3px;border-right:1px solid #b7c04a;border-top:1px solid #b7c04a;transform:rotate(45deg)}

  .gallery-arrows{left:917px;top:882px;display:flex;gap:2px}

  .site-footer{left:0;top:1120px;width:1067px;height:80px;background:var(--footer);color:var(--footer-text);font-size:11px}
  .footer-links{left:107px;top:22px}
  .copyright{left:107px;top:49px}
  .social{left:824px;top:23px;display:flex;gap:7px}
  .social span{width:29px;height:29px;border-radius:50%;background:var(--olive)}
</style>
</head>
<body>

<header class="abs site-header">
  <div class="abs brand-name">Altura Homes</div>
  <nav class="abs main-nav">
    <a class="active" href="#">Home</a>
    <a href="#">Tranquil Cliff Suites</a>
    <a href="#">The Apartment</a>
  </nav>
</header>

<section class="abs hero" role="img" aria-label="Aerial photo of the Barra da Tijuca coastline, beach, high-rise buildings, lagoon and green hills"></section>
<div class="abs hero-fact" style="top:178px">251 SQ M</div>
<div class="abs hero-fact" style="top:230px">Duplex Penthouse</div>
<div class="abs hero-fact" style="top:283px">4 Suites</div>
<div class="abs hero-fact" style="top:335px">Price R$ 2.200.000</div>
<div class="abs hero-fact highlight" style="top:389px">Price per SQ M: R$ 8.764</div>
<div class="abs slider-dots"><i></i><i></i><i></i><i class="current"></i></div>

<h1 class="abs section-title" style="top:558px">Welcome to <em>Penthouse !</em></h1>
<div class="abs hatch" style="top:598px;width:588px"></div>

<div class="abs photo-frame" style="left:106px;top:622px;width:224px;height:224px">
  <div role="img" aria-label="Photo of the condominium entrance with balconies above" style="background:linear-gradient(180deg,#6d6f74 0%,#8a6a5a 35%,#7a5a4c 55%,#6f8a5a 80%,#5f6a50 100%)"></div>
</div>

<div class="abs intro-text">
  <p>Sed ut perspiciatis unde omnis iste natus error sit voluptatem accusantium doloremque laudantium, totam rem aperiam, eaque ipsa quae ab illo inventore veritatis et quasi architecto beatae vitae dicta sunt explicabo. Nemo enim ipsam voluptatem quia voluptas sit aspernatur aut odit aut fugit, sed quia consequuntur magni dolores eos qui ratione voluptatem sequi nesciunt.</p>
  <p>Neque porro quisquam est, qui dolorem ipsum quia dolor sit amet, consectetur, adipisci velit, sed quia non numquam eius modi tempora incidunt</p>
  <p>ut labore et dolore magnam aliquam quaerat voluptatem. Ut enim ad minima veniam, quis nostrum exercitationem ullam corporis suscipit laboriosam, nisi ut aliquid ex ea commodi consequatur? Quis autem vel eum iure reprehenderit qui in ea voluptate velit esse quam nihil molestiae consequatur, vel illum qui dolorem eum fugiat quo voluptas nulla pariatur</p>
</div>

<aside class="abs features">
  <h2>Other Features</h2>
  <ul>
    <li>maids room with bath</li>
    <li>guest bathroom</li>
    <li>living room</li>
    <li>dinning room</li>
    <li>Terrace with heated pool for year round use Veranda</li>
  </ul>
</aside>

<h2 class="abs section-title" style="top:874px">Welcome to <em>Penthouse !</em></h2>
<svg class="abs gallery-arrows" width="40" height="20" viewBox="0 0 40 20" aria-label="Previous and next">
  <circle cx="9" cy="10" r="9" fill="#a7a9a8"/>
  <path d="M11 5 L6 10 L11 15" stroke="#fff" stroke-width="2.4" fill="none"/>
  <circle cx="30" cy="10" r="9" fill="#a7a9a8"/>
  <path d="M28 5 L33 10 L28 15" stroke="#fff" stroke-width="2.4" fill="none"/>
</svg>
<div class="abs hatch" style="top:914px;width:858px"></div>

<div class="abs photo-frame" style="left:106px;top:932px;width:197px;height:152px">
  <div role="img" aria-label="Photo of the living room with staircase and holiday tree" style="background:linear-gradient(180deg,#d8d4ca 0%,#b9aa95 50%,#5a3a28 100%)"></div>
</div>
<div class="abs photo-frame" style="left:325px;top:932px;width:196px;height:152px">
  <div role="img" aria-label="Photo of the lounge with orchids, artwork and wooden staircase" style="background:linear-gradient(180deg,#d2c8b4 0%,#b49a7a 55%,#5e3a22 100%)"></div>
</div>
<div class="abs photo-frame" style="left:544px;top:932px;width:196px;height:152px">
  <div role="img" aria-label="Photo of the terrace pool with sun loungers" style="background:linear-gradient(180deg,#8a8e96 0%,#4a4e56 45%,#2f9ad0 75%,#b9b3aa 100%)"></div>
</div>
<div class="abs photo-frame" style="left:763px;top:932px;width:197px;height:152px">
  <div role="img" aria-label="Photo of the rooftop veranda with barbecue and hill view" style="background:linear-gradient(180deg,#c8cfd6 0%,#a4a79a 45%,#d6d2cc 70%,#bdb8b1 100%)"></div>
</div>

<footer class="abs site-footer">
  <div class="abs footer-links">Home | Tranquil Cliff Suites | The Apartment</div>
  <div class="abs copyright">2013 © Penthouse. All Rights Reserved.</div>
  <div class="abs social">
    <span role="img" aria-label="Pebblenet"></span>
    <span role="img" aria-label="Chirpline"></span>
    <span role="img" aria-label="Reelhub"></span>
    <span role="img" aria-label="Inkpost"></span>
  </div>
</footer>

</body>
</html>
```